Business Card Design Project

I need a business card designed from scratch. I have an existing logo that I can upload in Illustrator for modification or redesign.

The Company is called Query Lanterns http://querylanterns.com.au and we provide Search Engine Optimization services to Australian businesses. The current logo signifies an increase in visitors, profits etc...

There are no restrictions as to the redesign - colours, style etc are all open to change.

Cards will be full colour and one sided printed at http://www.cardmoxel.com.au so check their requirements for file format and sizes etc.

I will expect all original files upon completion of project.

Target Market(s)

Any business with a web site looking to improve their search engine rankings

Industry/Entity Type

Business

Requirements
Must have
• I like modern, sleek designs. Clean, not fussy, uncluttered.

```html
<!DOCTYPE html>
<html lang="en">
<head>
<meta charset="utf-8">
<title>Query Lanterns – Business Card</title>
<link href="https://fonts.googleapis.com/css2?family=Source+Sans+3:wght@400;600;700&display=swap" rel="stylesheet">
<style>
  :root {
    --backdrop: #ece9e4;
    --card-white: #ffffff;
    --brand-blue: #1672b8;
    --ink: #3a3a3a;
    --icon-blue: #1a5fa0;
    --on-blue: #ffffff;
  }
  * { margin: 0; padding: 0; box-sizing: border-box; }
  html, body {
    width: 1200px; height: 460px; overflow: hidden;
    background: var(--backdrop);
    font-family: "Source Sans 3", sans-serif;
  }
  .canvas { position: relative; width: 1200px; height: 460px; }
  .card {
    position: absolute; top: 75px; height: 310px;
    border-radius: 14px;
  }
  .card-front { left: 36px; width: 540px; background: var(--card-white); }
  .card-back { left: 623px; width: 545px; background: var(--brand-blue); }

  .brand-name {
    position: absolute; left: 40px; top: 38px;
    display: flex; align-items: center; gap: 12px;
    color: var(--brand-blue); font-weight: 700; font-size: 40px; line-height: 1;
  }
  .brand-dot { width: 22px; height: 22px; border-radius: 50%; background: var(--brand-blue); }

  .address {
    position: absolute; left: 34px; top: 155px;
    font-size: 13.5px; line-height: 18px; color: var(--ink);
  }
  .contacts {
    position: absolute; left: 34px; top: 206px; list-style: none;
    font-size: 13.5px; line-height: 19px; color: var(--ink);
  }
  .contacts li { display: flex; align-items: center; gap: 5px; }
  .contacts svg { width: 10px; height: 10px; fill: var(--icon-blue); flex: none; }

  .person {
    position: absolute; left: 357px; top: 208px;
    color: var(--ink); font-size: 13.5px;
  }
  .person-name { color: var(--brand-blue); font-weight: 700; font-size: 17px; }

  .back-name {
    position: absolute; left: 0; right: 0; top: 112px;
    display: flex; justify-content: center; align-items: center; gap: 12px;
    color: var(--on-blue); font-weight: 700; font-size: 40px; line-height: 1;
  }
  .back-name .brand-dot { background: var(--on-blue); }
  .back-url {
    position: absolute; left: 0; right: 0; top: 221px; text-align: center;
    color: var(--on-blue); font-size: 14px; letter-spacing: 1px;
  }
</style>
</head>
<body>
<main class="canvas">
  <section class="card card-front">
    <div class="brand-name"><span class="brand-dot"></span>Query Lanterns</div>

    <address class="address" style="font-style:normal">
      00Floor Street, City Name<br>
      State Name, Contry Name
    </address>

    <ul class="contacts">
      <li><svg viewBox="0 0 10 10"><path d="M2 0.5 L3.8 2.6 L2.9 3.8 Q4 6 6.2 7.1 L7.4 6.2 L9.5 8 L8.3 9.5 Q1 8.5 0.5 1.7 Z"/></svg>098 765 4321</li>
      <li><svg viewBox="0 0 10 10"><rect x="2.5" y="0.5" width="5" height="9" rx="1"/><rect x="3.4" y="1.6" width="3.2" height="5" fill="#fff"/></svg>098 765 4321</li>
      <li><svg viewBox="0 0 10 10"><rect x="0.5" y="2" width="9" height="6.5"/><path d="M0.5 2 L5 5.5 L9.5 2" stroke="#fff" stroke-width="1" fill="none"/></svg>enquiry@querylanterns.com.au</li>
      <li><svg viewBox="0 0 10 10"><circle cx="5" cy="5" r="4.5"/><path d="M0.5 5 H9.5 M5 0.5 Q2.5 5 5 9.5 Q7.5 5 5 0.5" stroke="#fff" stroke-width="0.8" fill="none"/></svg>www.querylanterns.com.au</li>
    </ul>

    <p class="person"><span class="person-name">Your Name</span> Title</p>
  </section>

  <section class="card card-back">
    <div class="back-name"><span class="brand-dot"></span>Query Lanterns</div>
    <p class="back-url">www.querylanterns.com.au</p>
  </section>
</main>
</body>
</html>
```